Communication and Marketing agency needs a new presentation card

We are a group of communication and marketing agencies specialized in companies that are in the logistics and industrial sector. The head agency is TELVANO Grupo and the group consists of 4 agencies: TELVANO Media, TELVANO Digital, TELVANO Research and DifundeEnPantalla. We hace 4 offices in Spain (Madrid, Barcelona, Valencia and Murcia). We are looking for a clean and attractive design that transmits our experience, brand presence in the market and knowledge to those who receive the card.It has to maintain the colors of the logo that is attached.
Target Market(s)
logistics and industrial sector
Marketing department
Contact Information for Business Card
Clean and attractive design

```html
<!DOCTYPE html>
<html lang="es">
<head>
<meta charset="utf-8">
<title>TELVANO Grupo – Tarjeta de presentación</title>
<link href="https://fonts.googleapis.com/css2?family=Poppins:wght@300;400;500;600&display=swap" rel="stylesheet">
<style>
  :root {
    --bg: #a9a9a9;
    --card-dark: #2f2a29;
    --card-light: #ffffff;
    --brand-red: #b71c2a;
    --ink: #222222;
    --muted: #8d8d8d;
    --white: #ffffff;
  }
  * { box-sizing: border-box; margin: 0; padding: 0; }
  html, body {
    width: 1200px; height: 930px; overflow: hidden;
    background: var(--bg);
    font-family: "Poppins", sans-serif;
  }
  .stage {
    position: relative; width: 1200px; height: 930px;
    display: flex; align-items: center; justify-content: center; gap: 40px;
  }
  .card {
    position: relative; width: 540px; height: 346px;
    border-radius: 22px; overflow: hidden;
    box-shadow: 0 10px 24px rgba(0,0,0,.25);
  }

  /* Back side */
  .card--back { background: var(--card-dark); color: var(--white); }
  .office-map {
    position: absolute; left: 150px; top: 30px; width: 300px; height: 190px;
    border-radius: 40px 70px 30px 60px;
    background: radial-gradient(ellipse at 50% 45%, #8c8887 0%, #5a5554 60%, rgba(47,42,41,0) 100%);
  }
  .office-list {
    position: absolute; left: 0; right: 0; top: 236px;
    text-align: center; font-size: 15px; font-weight: 600; letter-spacing: .3px;
  }
  .agency-row {
    position: absolute; left: 22px; right: 22px; bottom: 28px;
    display: flex; justify-content: space-between; align-items: baseline;
  }
  .agency-name { font-size: 13px; font-weight: 500; color: var(--muted); letter-spacing: .5px; }
  .agency-name--accent { color: var(--brand-red); }

  /* Front side */
  .card--front { background: var(--card-light); color: var(--ink); }
  .brand-name {
    position: absolute; left: 38px; top: 102px;
    font-size: 30px; line-height: 40px; font-weight: 500; color: var(--brand-red); letter-spacing: .5px;
  }
  .holder { position: absolute; right: 34px; top: 44px; text-align: right; }
  .holder-name { font-size: 21px; line-height: 30px; font-weight: 600; color: var(--brand-red); }
  .holder-role { font-size: 12px; line-height: 16px; color: var(--ink); margin-top: 2px; }
  .holder-rule { position: absolute; right: 34px; top: 98px; width: 160px; height: 1.5px; background: var(--brand-red); }
  .section-rule { position: absolute; top: 152px; height: 1.5px; }
  .section-rule--dark { left: 38px; width: 232px; background: var(--ink); }
  .section-rule--red { left: 274px; width: 232px; background: var(--brand-red); }
  .contact-rule { position: absolute; left: 34px; top: 200px; width: 300px; height: 1.5px; background: var(--ink); }
  .contact-list {
    position: absolute; left: 34px; top: 208px; list-style: none;
    font-size: 14px; line-height: 22px; color: var(--ink);
  }
  .contact-list li { display: flex; align-items: center; gap: 9px; }
  .contact-icon { width: 11px; height: 11px; flex: none; }
  .swoosh { position: absolute; left: 0; bottom: 0; width: 540px; height: 150px; }
</style>
</head>
<body>
<main class="stage">

  <section class="card card--back" aria-label="Reverso de la tarjeta">
    <div class="office-map" role="img" aria-label="Mapa de puntos de España con las cuatro oficinas marcadas"></div>
    <p class="office-list">Madrid | Barcelona | Valencia | Murcia</p>
    <div class="agency-row">
      <span class="agency-name">TELVANO Digital</span>
      <span class="agency-name agency-name--accent">DifundeEnPantalla</span>
      <span class="agency-name">TELVANO Media</span>
      <span class="agency-name">TELVANO Research</span>
    </div>
  </section>

  <section class="card card--front" aria-label="Anverso de la tarjeta">
    <div class="holder">
      <div class="holder-name">Álvaro Estrella</div>
      <div class="holder-role">Director</div>
    </div>
    <div class="holder-rule"></div>

    <div class="brand-name">TELVANO Grupo</div>
    <div class="section-rule section-rule--dark"></div>
    <div class="section-rule section-rule--red"></div>

    <div class="contact-rule"></div>
    <ul class="contact-list">
      <li>
        <svg class="contact-icon" viewBox="0 0 12 12"><path d="M2 1l2 0 1 3-1.5 1a6 6 0 0 0 3.5 3.5L8 7l3 1 0 2c0 1-1 1-1 1C5 11 1 7 1 2c0 0 0-1 1-1z" fill="#b71c2a"/></svg>
        910 472 318
      </li>
      <li>
        <svg class="contact-icon" viewBox="0 0 12 12"><rect x="3" y="0.5" width="6" height="11" rx="1.2" fill="none" stroke="#b71c2a" stroke-width="1.4"/><circle cx="6" cy="9.5" r=".8" fill="#b71c2a"/></svg>
        600 214 775
      </li>
      <li>
        <svg class="contact-icon" viewBox="0 0 12 12"><rect x="0.7" y="2.2" width="10.6" height="7.6" rx="1" fill="none" stroke="#b71c2a" stroke-width="1.4"/><path d="M1 3l5 3.6L11 3" fill="none" stroke="#b71c2a" stroke-width="1.2"/></svg>
        aestrella@telvano.es
      </li>
      <li>
        <svg class="contact-icon" viewBox="0 0 12 12"><circle cx="6" cy="6" r="5" fill="none" stroke="#b71c2a" stroke-width="1.3"/><path d="M1 6h10M6 1c2.5 3 2.5 7 0 10M6 1c-2.5 3-2.5 7 0 10" fill="none" stroke="#b71c2a" stroke-width="1"/></svg>
        www.telvano.es
      </li>
      <li>
        <svg class="contact-icon" viewBox="0 0 12 12"><rect x="1.5" y="1.5" width="9" height="9" fill="#b71c2a"/></svg>
        alvaroestrella
      </li>
    </ul>

    <svg class="swoosh" viewBox="0 0 540 150" preserveAspectRatio="none" aria-hidden="true">
      <path d="M150 150 L392 150 C410 150 420 120 440 110 C460 100 500 100 540 100 L540 150 Z" fill="#b71c2a"/>
      <path d="M150 140 L385 140 C405 140 418 112 436 104 L540 92 L540 98 L440 108 C422 116 410 146 388 146 L150 146 Z" fill="#222222"/>
      <path d="M150 134 L380 134 C400 134 414 106 432 98 L540 86 L540 90 L434 102 C416 110 402 138 382 138 L150 138 Z" fill="#ffffff"/>
    </svg>
  </section>

</main>
</body>
</html>
```